Re-style home page - eye-catching and unique design for social commerce website

We need a new concept design for BrinoKet's home page.
We don't want to make huge changes but creating a more professional and eye-catching style.

We need to look very serious like a professional services company and in the same time to look like a social network for e-commerce.

Our logo is very captive and you can use to creating something of harmonious.

This is a re-style and I'm excepted to see unique and fresh design like Glimmora.

Target Market(s)

e-commerce and social

Industry/Entity Type

Social

Number of Pages Required

1 page

Font styles to use
Serif
Sans Serif

Requirements
Must have
• An eye-catching result.
• Search bar with logo and Login How it works and business
• The slogan with login and signup.
• Footer links.
Nice to have
• I would like to open the home page and see only two clear ways:
• -Consumer
• --Search
• --The slogan
• --Login and Signup
• --How it works
• -Business
• --Go to Business area
• Background: City, Shopping.
Should not have
• Scrollbar style!

```html
<!DOCTYPE html>
<html lang="en">
<head>
<meta charset="utf-8">
<title>BrinoKet – Shop directly from your profile</title>
<link rel="stylesheet" href="https://fonts.googleapis.com/css2?family=Montserrat:wght@400;600;700&family=Open+Sans:wght@300;400;600&display=swap">
<style>
:root{
  --night:#1d1d45;
  --night-deep:#15163a;
  --haze:#4a4a7c;
  --header-bg:rgba(18,20,48,0.62);
  --field-dark:rgba(255,255,255,0.12);
  --white:#ffffff;
  --ink:#2e2e38;
  --muted:#9a9ab0;
  --red:#d2302f;
  --green:#7cb72e;
}
*{box-sizing:border-box;margin:0;padding:0}
html,body{width:1200px;height:675px;overflow:hidden;background:var(--night)}
.stage{position:relative;width:1200px;height:675px;overflow:hidden;font-family:"Open Sans",Arial,sans-serif;color:var(--white)}
.city-backdrop{position:absolute;inset:0;
  background:
    radial-gradient(ellipse at 20% 35%,rgba(150,130,170,0.45),transparent 55%),
    radial-gradient(ellipse at 80% 30%,rgba(140,140,190,0.4),transparent 55%),
    radial-gradient(ellipse at 60% 80%,rgba(90,70,110,0.5),transparent 60%),
    linear-gradient(180deg,#3c3c6a 0%,#45406e 45%,#2a2850 75%,#1b1b40 100%);}
.site-header{position:absolute;left:0;top:0;width:1200px;height:59px;background:var(--header-bg);border-bottom:1px solid rgba(255,255,255,0.06)}
.brand{position:absolute;left:27px;top:12px;font-family:"Montserrat",Arial,sans-serif;font-weight:700;font-size:28px;line-height:34px;color:var(--white);display:flex;align-items:center;gap:8px}
.brand-dot{width:14px;height:14px;border-radius:50%;background:var(--white)}
.search-field{position:absolute;left:411px;top:11px;width:400px;height:36px;background:var(--field-dark);border-radius:3px;padding:0 17px;font-size:13px;line-height:36px;color:var(--muted)}
.search-icon{position:absolute;left:829px;top:20px}
.login-link{position:absolute;left:871px;top:20px;font-family:"Montserrat",Arial,sans-serif;font-weight:600;font-size:12.5px;line-height:18px;color:var(--white)}
.hero-illustration{position:absolute;left:474px;top:110px;width:278px;height:182px;border-radius:10px;
  background:radial-gradient(ellipse at 50% 55%,#1b1c3e 0%,rgba(36,38,80,0.8) 45%,rgba(70,70,120,0.15) 80%,transparent 100%)}
.slogan{position:absolute;left:0;top:331px;width:1200px;text-align:center;font-weight:300;font-size:35px;line-height:48px;color:var(--white)}
.feed-label{position:absolute;left:329px;top:404px;font-family:"Montserrat",Arial,sans-serif;font-weight:600;font-size:10.5px;line-height:16px}
.select{position:absolute;top:395px;width:176px;height:34px;background:var(--white);border-radius:2px;color:var(--ink);font-size:11.5px;line-height:34px;padding-left:13px}
.select svg.chevron{position:absolute;right:12px;top:13px}
.select-interest{left:433px}
.select-city{left:618px;padding-left:28px}
.select-city svg.pin{position:absolute;left:11px;top:10px}
.btn{position:absolute;border-radius:2px;font-family:"Montserrat",Arial,sans-serif;font-weight:600;color:var(--white);text-align:center;display:flex;align-items:center;justify-content:center;gap:8px}
.btn-signup{left:807px;top:395px;width:84px;height:34px;background:var(--red);font-size:12.5px}
.btn-business{left:511px;top:459px;width:179px;height:34px;background:var(--green);font-size:12px}
.how-link{position:absolute;left:0;top:504px;width:1200px;text-align:center;font-family:"Montserrat",Arial,sans-serif;font-weight:600;font-size:11.5px;line-height:16px}
.footer-nav{position:absolute;left:0;top:574px;width:1200px;display:flex;justify-content:center;gap:0;font-family:"Montserrat",Arial,sans-serif;font-weight:600;font-size:10.5px;line-height:16px}
.footer-nav a{color:var(--white);text-decoration:none;margin:0 16px}
.copyright{position:absolute;left:0;top:602px;width:1200px;text-align:center;font-family:"Montserrat",Arial,sans-serif;font-weight:600;font-size:9.5px;line-height:14px}
</style>
</head>
<body>
<div class="stage">
  <div class="city-backdrop" role="img" aria-label="Blurred photograph of a busy city shopping street full of people"></div>

  <header class="site-header">
    <div class="brand"><span>BrinoKet</span><span class="brand-dot"></span></div>
    <div class="search-field">Search keyword</div>
    <svg class="search-icon" width="20" height="20" viewBox="0 0 20 20" aria-hidden="true">
      <circle cx="8.5" cy="8.5" r="6.5" fill="none" stroke="#fff" stroke-width="2.4"/>
      <line x1="13.3" y1="13.3" x2="18" y2="18" stroke="#fff" stroke-width="2.6" stroke-linecap="round"/>
    </svg>
    <a class="login-link">Login</a>
  </header>

  <div class="hero-illustration" role="img" aria-label="Illustration of a laptop showing a shopping cart on a store page, connected by dotted lines to round profile avatars"></div>

  <h1 class="slogan">Shop directly from your profile</h1>

  <div class="feed-label">Setup your feed</div>
  <div class="select select-interest">Active life
    <svg class="chevron" width="13" height="8" viewBox="0 0 13 8" aria-hidden="true"><polyline points="1,1 6.5,6.5 12,1" fill="none" stroke="#b5b5c0" stroke-width="1.4"/></svg>
  </div>
  <div class="select select-city">
    <svg class="pin" width="10" height="14" viewBox="0 0 10 14" aria-hidden="true"><path d="M5 0C2.2 0 0 2.2 0 5c0 3.6 5 9 5 9s5-5.4 5-9c0-2.8-2.2-5-5-5zm0 7a2 2 0 1 1 0-4 2 2 0 0 1 0 4z" fill="#b5b5c0"/></svg>
    London
    <svg class="chevron" width="13" height="8" viewBox="0 0 13 8" aria-hidden="true"><polyline points="1,1 6.5,6.5 12,1" fill="none" stroke="#b5b5c0" stroke-width="1.4"/></svg>
  </div>
  <a class="btn btn-signup">Sign Up</a>

  <a class="btn btn-business">Go to Business Area
    <svg width="18" height="8" viewBox="0 0 18 8" aria-hidden="true"><line x1="0" y1="4" x2="16" y2="4" stroke="#fff" stroke-width="1.2"/><polyline points="12.5,0.8 16.5,4 12.5,7.2" fill="none" stroke="#fff" stroke-width="1.2"/></svg>
  </a>
  <div class="how-link">How it works</div>

  <nav class="footer-nav">
    <a>About Us</a><a>Blog</a><a>Business</a><a>Jobs</a><a>Privacy</a><a>FAQ</a><a>Contacts</a>
  </nav>
  <div class="copyright">© 2015 BrinoKet. All right reserved.</div>
</div>
</body>
</html>
```